Verodex business card

Business card for sustainable investment company called "Verodex". Verodex is an exchange platform selling carbon credits between buyers and sellers. Carbon Credits are an environmental commodity for reducing global carbon emissions.

the card should obviously have our logo and the theme should be sustainability/environment mixed with a trading platform.

Contact Information for Business Card

Logo, Name, Title, Phone, Email

Colors
0054AA
0677BA
7BADD7
CADEEF
E8F1F8
0094D4
00A9DD
6FCCEA
C7EBF8
E9F6FB
00AB8E
00BBA5
67D7C9
C6EFE9
E9F9F6
59FF00
82FF00
B8FF75
E3FFCB
F4FFEA

```html
<!DOCTYPE html>
<html lang="en">
<head>
<meta charset="UTF-8">
<title>Verodex Business Card</title>
<link href="https://fonts.googleapis.com/css2?family=Open+Sans:wght@400;600;700&display=swap" rel="stylesheet">
<style>
  :root {
    --stage: #222222;
    --navy: #142a50;
    --white: #ffffff;
    --mark: #4fa6d6;
    --wave-light: #6fccea;
    --wave-mid: #4fa8d4;
    --wave-deep: #4a7ec8;
  }
  * { margin: 0; padding: 0; box-sizing: border-box; }
  html, body {
    width: 1200px; height: 780px; overflow: hidden;
    background: var(--stage);
    font-family: "Open Sans", Arial, sans-serif;
  }
  .stage {
    width: 1200px; height: 780px;
    display: flex; align-items: center; justify-content: center; gap: 40px;
  }
  .card {
    position: relative;
    width: 540px; height: 310px;
    border-radius: 22px;
    overflow: hidden;
    box-shadow: 0 14px 30px rgba(0,0,0,0.55);
  }
  .card-front { background: var(--navy); display: flex; align-items: center; justify-content: center; }
  .card-back { background: var(--white); }

  .brand { display: flex; align-items: center; gap: 14px; }
  .brand-square { width: 34px; height: 34px; background: var(--mark); border-radius: 4px; }
  .brand-name {
    font-weight: 700; letter-spacing: 3px;
    color: var(--white); font-size: 44px; line-height: 1;
  }
  .card-back .brand { position: absolute; top: 40px; right: 40px; gap: 10px; }
  .card-back .brand-square { width: 24px; height: 24px; }
  .card-back .brand-name { color: var(--navy); font-size: 30px; letter-spacing: 2px; }

  .wave { position: absolute; inset: 0; width: 540px; height: 310px; }

  .contact {
    position: absolute; left: 52px; top: 168px;
    color: var(--white);
  }
  .person-name { font-size: 18px; font-weight: 700; line-height: 1.15; }
  .person-title { font-size: 12px; font-weight: 600; line-height: 1.3; margin-bottom: 6px; }
  .address { font-size: 11px; line-height: 1.35; margin-bottom: 8px; }
  .contact-list { list-style: none; font-size: 11px; line-height: 1.45; }
  .contact-list li { display: flex; align-items: center; gap: 7px; }
  .contact-list svg { width: 11px; height: 11px; flex: none; }
</style>
</head>
<body>
<main class="stage">

  <section class="card card-front" aria-label="Card front">
    <div class="brand">
      <span class="brand-square"></span>
      <span class="brand-name">VERODEX</span>
    </div>
  </section>

  <section class="card card-back" aria-label="Card back">
    <div class="brand">
      <span class="brand-square"></span>
      <span class="brand-name">VERODEX</span>
    </div>

    <svg class="wave" viewBox="0 0 540 310" aria-hidden="true">
      <defs>
        <linearGradient id="waveGradient" x1="0" y1="0" x2="1" y2="0">
          <stop offset="0" stop-color="var(--wave-light)"/>
          <stop offset="0.55" stop-color="var(--wave-mid)"/>
          <stop offset="1" stop-color="var(--wave-deep)"/>
        </linearGradient>
      </defs>
      <path d="M0,132 C120,116 240,114 330,116 C420,118 480,96 540,68 L540,310 L0,310 Z" fill="var(--navy)"/>
      <path d="M0,144 C110,124 230,122 330,126 C430,130 490,106 540,84 L540,102 C480,128 410,140 320,140 C220,140 110,146 30,158 L0,164 Z" fill="url(#waveGradient)"/>
      <path d="M0,140 C110,120 230,119 330,122 C430,126 490,102 540,78" fill="none" stroke="var(--white)" stroke-width="3"/>
      <path d="M20,158 C110,142 220,138 320,140 C410,142 480,128 540,100" fill="none" stroke="var(--white)" stroke-width="2.5"/>
    </svg>

    <div class="contact">
      <p class="person-name">Lena Marovic</p>
      <p class="person-title">Co-Founder</p>
      <p class="address">1840 Elmridge Ave. Suite 300<br>Dallas, TX 75201</p>
      <ul class="contact-list">
        <li>
          <svg viewBox="0 0 24 24"><path fill="#fff" d="M6.6 10.8a15.1 15.1 0 0 0 6.6 6.6l2.2-2.2c.3-.3.7-.4 1-.2 1.1.4 2.3.6 3.6.6.6 0 1 .4 1 1V20c0 .6-.4 1-1 1C10.6 21 3 13.4 3 4c0-.6.4-1 1-1h3.5c.6 0 1 .4 1 1 0 1.3.2 2.5.6 3.6.1.3 0 .7-.2 1z"/></svg>
          (555) 214-6038
        </li>
        <li>
          <svg viewBox="0 0 24 24"><rect x="2" y="5" width="20" height="14" rx="2" fill="#fff"/><path d="M3 6l9 7 9-7" fill="none" stroke="#142a50" stroke-width="2"/></svg>
          hello@verodex-mail.com
        </li>
        <li>
          <svg viewBox="0 0 24 24"><circle cx="12" cy="12" r="9.5" fill="none" stroke="#fff" stroke-width="2"/><ellipse cx="12" cy="12" rx="4" ry="9.5" fill="none" stroke="#fff" stroke-width="1.6"/><path d="M3 12h18" stroke="#fff" stroke-width="1.6"/></svg>
          www.verodex-exchange.com
        </li>
      </ul>
    </div>
  </section>

</main>
</body>
</html>
```